Gala Dinner Flyer for State Water Polo Association

We need a promotional flyer for the "2016 Coral Soiree" - a fundraising gala dinner for Tidewave Sport Collective to distribute to our members.

The details for the event are as follows:

Date: Saturday 16th April 2016
Time: 7pm to Midnight
Venue: Marlowe C, Brindle Wharf, 84 Tamsin Parade, Docklands 3008
Cost: $150 per person
Details: Canapés on arrival followed by a three course dinner, with premium beverages throughout the evening.
RSVP: Friday 8th April 2016
Dress Code: Black Tie
For tickets for to www.tixmondo.com.au/tickets/event/coralsoiree

We also require an event logo with a minimum height of 200px, and event background with a minimum width of 1200px and height of 800px, and flyer image with a minimum width of 620px and height of 874px.

I have attached a number of logos we need incorporated along with last years invitation and a few photos from last years event.

We would like to use designs that use water and the colour blue.

The final design should communicate elegance and high class

Target Market(s)

25-60 year old Men and Women from affluent families

Industry/Entity Type

Promotional

Colors
1861ab
3277b5
85acd3
cedeed
ffffff

Requirements
Must have
• Tidewave Sport Collective Logo, Southern Herons Logo, quietharbor Logo & Kestrel Holdings Logo

```html
<!DOCTYPE html>
<html lang="en">
<head>
<meta charset="utf-8">
<title>2016 Coral Soiree – Gala Dinner Flyer</title>
<link rel="stylesheet" href="https://fonts.googleapis.com/css2?family=Great+Vibes&family=Raleway:wght@200;300;500;600;700&display=swap">
<style>
  :root {
    --blue-deep: #1861ab;
    --blue-mid: #3277b5;
    --blue-soft: #85acd3;
    --blue-pale: #cedeed;
    --white: #ffffff;
    --ink: #050608;
    --grey-row: #d9dbde;
    --grey-row-dark: #b9bcc1;
    --text-dark: #1c1f24;
  }
  * { box-sizing: border-box; margin: 0; padding: 0; }
  html, body { width: 849px; height: 1200px; overflow: hidden; background: var(--ink); }
  body { font-family: "Raleway", Arial, sans-serif; color: var(--white); position: relative; }

  .hero { position: absolute; left: 0; top: 0; width: 849px; height: 620px; }

  .event-title { position: absolute; left: 0; top: 140px; width: 849px; text-align: center; }
  .event-title .year { display: block; font-weight: 300; font-size: 44px; letter-spacing: 4px; color: var(--blue-soft); }
  .event-title .name-main { display: block; font-weight: 200; font-size: 104px; letter-spacing: 10px; line-height: 1; color: var(--white); text-transform: uppercase; margin-top: 4px; }
  .event-title .name-script { display: block; font-family: "Great Vibes", cursive; font-size: 92px; line-height: 1; color: var(--white); margin-top: -6px; }

  .date-ribbon { position: absolute; left: 40px; top: 505px; width: 770px; height: 90px; }
  .date-ribbon-text { position: absolute; left: 0; top: 516px; width: 849px; text-align: center; font-weight: 500; font-size: 38px; letter-spacing: 2px; text-transform: uppercase; color: var(--white); }

  .details { position: absolute; left: 120px; top: 612px; width: 610px; }
  .detail-row { display: flex; height: 52px; margin-bottom: 10px; }
  .detail-label { width: 170px; background: linear-gradient(var(--blue-mid), var(--blue-deep)); display: flex; align-items: center; padding-left: 28px; font-weight: 600; font-size: 19px; letter-spacing: 2px; text-transform: uppercase; clip-path: polygon(14px 0, 100% 0, 100% 100%, 0 100%); }
  .detail-value { flex: 1; background: linear-gradient(var(--grey-row), var(--grey-row-dark)); color: var(--text-dark); display: flex; flex-direction: column; justify-content: center; padding: 0 26px; font-weight: 700; font-size: 16px; text-transform: uppercase; letter-spacing: 0.5px; }
  .detail-value.centered { align-items: center; }
  .detail-value small { font-weight: 500; font-size: 11px; text-transform: none; letter-spacing: 0; margin-top: 2px; }
  .detail-value.paragraph { font-weight: 500; font-size: 12.5px; text-transform: none; letter-spacing: 0; line-height: 1.35; }

  .tickets { position: absolute; left: 0; top: 998px; width: 849px; text-align: center; font-size: 17px; font-weight: 500; }
  .tickets .lead { color: var(--blue-soft); font-weight: 700; text-transform: uppercase; letter-spacing: 1px; }
  .tickets .url { font-weight: 700; }

  .partners { position: absolute; left: 90px; top: 1048px; width: 670px; height: 70px; display: flex; align-items: center; justify-content: space-between; }
  .partner { display: flex; align-items: center; gap: 8px; font-weight: 600; font-size: 13px; letter-spacing: 1px; color: var(--white); text-transform: uppercase; }
  .partner .dot { width: 14px; height: 14px; border-radius: 50%; background: var(--blue-mid); flex: none; }
</style>
</head>
<body>

<svg class="hero" viewBox="0 0 849 620" xmlns="http://www.w3.org/2000/svg">
  <defs>
    <linearGradient id="photoTone" x1="0" y1="0" x2="1" y2="1">
      <stop offset="0" stop-color="#5a5d62"/>
      <stop offset="0.5" stop-color="#26282c"/>
      <stop offset="1" stop-color="#0b0c0e"/>
    </linearGradient>
    <radialGradient id="bubbleTone" cx="0.5" cy="0.4" r="0.6">
      <stop offset="0" stop-color="#6a6e74"/>
      <stop offset="1" stop-color="#1a1c1f"/>
    </radialGradient>
  </defs>
  <rect x="0" y="0" width="849" height="500" fill="url(#photoTone)" role="img" aria-label="Black and white photographs of guests and the band at last year's gala"/>
  <g class="bubbles" role="img" aria-label="Photo bubbles of last year's event">
    <circle cx="70" cy="120" r="95" fill="url(#bubbleTone)" stroke="var(--blue-mid)" stroke-width="3"/>
    <circle cx="770" cy="90" r="90" fill="url(#bubbleTone)" stroke="var(--blue-mid)" stroke-width="3"/>
    <circle cx="790" cy="330" r="70" fill="url(#bubbleTone)" stroke="var(--blue-soft)" stroke-width="2"/>
    <circle cx="60" cy="380" r="60" fill="url(#bubbleTone)" stroke="var(--blue-soft)" stroke-width="2"/>
  </g>
  <g class="bubble-rings" fill="none">
    <circle cx="210" cy="40" r="40" stroke="var(--blue-mid)" stroke-width="2"/>
    <circle cx="640" cy="40" r="28" stroke="var(--blue-soft)" stroke-width="2"/>
    <circle cx="690" cy="470" r="30" stroke="var(--blue-mid)" stroke-width="2"/>
    <circle cx="160" cy="470" r="22" stroke="var(--blue-soft)" stroke-width="2"/>
    <circle cx="700" cy="230" r="16" fill="var(--blue-mid)"/>
    <circle cx="150" cy="250" r="12" fill="var(--blue-soft)"/>
    <circle cx="560" cy="20" r="10" fill="var(--blue-mid)"/>
  </g>
  <rect x="0" y="470" width="849" height="150" fill="var(--ink)" opacity="0.85"/>
  <circle class="title-disc" cx="425" cy="300" r="225" fill="var(--ink)" stroke="var(--blue-mid)" stroke-width="6"/>
  <circle cx="425" cy="300" r="237" fill="none" stroke="var(--blue-soft)" stroke-width="1.5" opacity="0.7"/>
</svg>

<h1 class="event-title">
  <span class="year">2016</span>
  <span class="name-main">Coral</span>
  <span class="name-script">Soiree</span>
</h1>

<svg class="date-ribbon" viewBox="0 0 770 90" xmlns="http://www.w3.org/2000/svg" aria-hidden="true">
  <defs>
    <linearGradient id="ribbonBlue" x1="0" y1="0" x2="0" y2="1">
      <stop offset="0" stop-color="var(--blue-mid)"/>
      <stop offset="1" stop-color="var(--blue-deep)"/>
    </linearGradient>
  </defs>
  <polygon points="0,20 40,20 40,85 0,85 18,52" fill="#0f3f73"/>
  <polygon points="770,20 730,20 730,85 770,85 752,52" fill="#0f3f73"/>
  <polygon points="20,75 40,75 40,90" fill="#0a2a4d"/>
  <polygon points="750,75 730,75 730,90" fill="#0a2a4d"/>
  <rect x="20" y="8" width="730" height="67" fill="url(#ribbonBlue)"/>
</svg>
<p class="date-ribbon-text">Saturday 16th April 2016</p>

<section class="details">
  <div class="detail-row"><div class="detail-label">Time</div><div class="detail-value centered">7.00pm till midnight</div></div>
  <div class="detail-row"><div class="detail-label">Venue</div><div class="detail-value">Marlowe C, Brindle Wharf<small>84 Tamsin Parade, Docklands VIC 3008</small></div></div>
  <div class="detail-row"><div class="detail-label">Details</div><div class="detail-value paragraph">Canapés on arrival followed by a three course dinner with premium beverages throughout the evening</div></div>
  <div class="detail-row"><div class="detail-label">Cost</div><div class="detail-value centered">$150 per person</div></div>
  <div class="detail-row"><div class="detail-label">Dress</div><div class="detail-value centered">Black tie</div></div>
  <div class="detail-row"><div class="detail-label">RSVP</div><div class="detail-value centered">Friday 8th April 2016</div></div>
</section>

<p class="tickets"><span class="lead">For tickets</span> go to <span class="url">www.tixmondo.com.au/tickets/event/coralsoiree</span></p>

<footer class="partners">
  <div class="partner"><span class="dot"></span>Southern Herons</div>
  <div class="partner"><span class="dot"></span>Tidewave Sport Collective</div>
  <div class="partner"><span class="dot"></span>quietharbor</div>
  <div class="partner"><span class="dot"></span>Kestrel Holdings</div>
</footer>

</body>
</html>
```